Website for my photography business

I need a website for my photography business, Bram Kellet Photography. I need a website that has a landing page with a cover photo of each kind of photography I do. For example, Nature, Weddings, Portraits and Architecture. I want it so that when someone comes onto my website they have to choose which kind of photography page they want to visit. So if they click on the wedding photo it will open to a page with my wedding portfolio images and a contact me button. If they choose nature photography I want them to be redirected to an e-commerce section where they can purchase prints. Architecture and Portraits should open up to their respective portfolios with about me and contact info. I like this kind of format because I want people who come to my website for a specific type of photography to be able to be directed there easily without having to look at a mix of other kinds of photography. I will provide a few files to use as placeholders. I have already purchased the bramkelletphotography.example domain name. A Wix website would be great because I am most familiar with it but I am open to anything.

Industry/Entity Type

Photographer

Number of Pages Required

5+ page

Requirements
Must have
• Landing Page and e-commerce

```html
<!DOCTYPE html>
<html lang="en">
<head>
<meta charset="utf-8">
<title>Bram Kellet Photography</title>
<link rel="stylesheet" href="https://fonts.googleapis.com/css2?family=Kalam:wght@400;700&family=Oswald:wght@600&family=Lato:wght@400;700&display=swap">
<style>
:root{
  --navy:#1c1a4a;
  --gold:#f7b52c;
  --orange:#f29a1f;
  --ink:#2a2a33;
  --light:#f2f2f2;
  --footer:#1d1d24;
  --white:#ffffff;
}
*{margin:0;padding:0;box-sizing:border-box}
html,body{width:1200px;height:3295px;overflow:hidden}
body{position:relative;background:var(--white);font-family:'Lato',sans-serif;color:var(--ink)}
.script{font-family:'Kalam',cursive}
.abs{position:absolute}

/* header */
.site-header{position:absolute;left:0;top:0;width:1200px;height:122px;background:var(--white)}
.brand{position:absolute;left:76px;top:42px;font-family:'Kalam',cursive;font-size:30px;color:var(--navy);line-height:1}
.main-nav{position:absolute;top:52px;left:0}
.main-nav a{position:absolute;white-space:nowrap;font-family:'Kalam',cursive;font-size:21px;color:var(--ink);text-decoration:none;line-height:1}
.main-nav a.active{color:var(--orange)}
.social{position:absolute;display:flex;gap:22px}
.social span{display:block;width:18px;height:18px;border-radius:50%;background:currentColor}
.header-social{left:992px;top:53px;color:#55565e}

/* hero */
.hero{position:absolute;left:0;top:122px;width:1200px;height:605px;
  background:linear-gradient(100deg,#23234f 0%,#3e3849 35%,#8a6a2e 65%,#d59c24 100%)}
.hero-hello{position:absolute;left:75px;top:300px;font-family:'Kalam',cursive;font-size:40px;color:var(--gold);line-height:1}
.hero-title{position:absolute;left:75px;top:358px;font-family:'Oswald',sans-serif;font-weight:600;font-size:92px;line-height:101px;color:var(--white);text-transform:uppercase;letter-spacing:-1px}

.landscape{position:absolute;left:0;top:727px;width:1200px;height:469px;
  background:linear-gradient(180deg,#b9a6c7 0%,#9585a8 30%,#4a3c4c 55%,#2d2b3d 70%,#7f87ac 85%,#b3bbd7 100%)}

/* portfolio */
.section-title{position:absolute;left:0;width:1200px;text-align:center;font-family:'Kalam',cursive;font-size:44px;line-height:1}
.tile{position:absolute;display:flex;align-items:center;justify-content:center}
.tile span{font-family:'Kalam',cursive;font-size:52px;color:var(--white);line-height:1}
.tile-nature{left:74px;top:1339px;width:691px;height:407px;background:linear-gradient(135deg,#2b3a2a 0%,#3f4a36 40%,#b0622b 55%,#2a3328 75%,#d9dde2 100%)}
.tile-weddings{left:780px;top:1339px;width:346px;height:407px;background:linear-gradient(150deg,#8c7a6c 0%,#6e6259 50%,#1f2333 70%,#9a8a7a 100%)}
.tile-portraits{left:74px;top:1763px;width:520px;height:407px;background:linear-gradient(180deg,#b7a049 0%,#8f7b3e 40%,#4b5a7e 75%,#3a4564 100%)}
.tile-architecture{left:606px;top:1763px;width:520px;height:407px;background:linear-gradient(180deg,#9fa4ab 0%,#8a5a44 35%,#a6988a 65%,#6d6f6c 100%)}

/* about */
.about{position:absolute;left:0;top:2241px;width:1200px;height:509px;background:var(--light)}
.about-text{position:absolute;left:200px;top:2419px;width:800px;text-align:center;font-size:25px;line-height:38.5px;color:var(--ink)}
.btn{position:absolute;display:flex;align-items:center;justify-content:center;background:var(--gold);color:var(--white);font-family:'Lato',sans-serif;font-weight:700;font-size:18px;width:150px;height:43px}

/* contact */
.contact{position:absolute;left:0;top:2750px;width:1200px;height:483px;background:var(--navy)}
.contact .section-title{color:var(--white)}
.field-label{position:absolute;font-size:13px;color:var(--white);line-height:1}
.field-line{position:absolute;height:1px;background:#8b8aa6}

/* footer */
.site-footer{position:absolute;left:0;top:3233px;width:1200px;height:62px;background:var(--footer)}
.copyright{position:absolute;left:75px;top:25px;font-size:11px;color:var(--white)}
.footer-social{left:914px;top:22px;color:var(--white);gap:22px}
</style>
</head>
<body>

<header class="site-header">
  <div class="brand">Bram Kellet Photography</div>
  <nav class="main-nav">
    <a class="active" style="left:461px">Home</a>
    <a style="left:559px">About Me</a>
    <a style="left:700px">Portfolio</a>
    <a style="left:825px">Contact Us</a>
  </nav>
  <div class="social header-social" aria-label="Social links"><span></span><span></span><span></span><span></span></div>
</header>

<section class="hero" role="img" aria-label="Photographer holding a camera up to the eye, toned in navy and gold"></section>
<div class="hero-hello">Hello,</div>
<h1 class="hero-title">Bram Kellet Photography<br>And I ‘m a photographer</h1>

<div class="landscape" role="img" aria-label="Panoramic mountain range reflected in still water under a dusk sky"></div>

<h2 class="section-title" style="top:1252px;color:var(--ink)">Portfolio</h2>
<a class="tile tile-nature" role="img" aria-label="Nature photography: a fox resting in snowy forest"><span>Nature</span></a>
<a class="tile tile-weddings" role="img" aria-label="Wedding photography: wedding rings on stone"><span>Weddings</span></a>
<a class="tile tile-portraits" role="img" aria-label="Portrait photography: family sitting in autumn leaves"><span>Portraits</span></a>
<a class="tile tile-architecture" role="img" aria-label="Architecture photography: brick and glass campus building"><span>Architecture</span></a>

<section class="about">
  <h2 class="section-title" style="top:86px;color:var(--ink)">About Me</h2>
</section>
<p class="about-text">Aliquam sagittis velit odio, maximus lacinia quam congue sit amet. Praesent diam sapien, feugiat a dolor nec, bibendum consectetur nibh. Ut magna massa, posuere quis libero nec, venenatis vestibulum quam.</p>
<a class="btn" style="left:524px;top:2612px">Contact Me</a>

<section class="contact">
  <h2 class="section-title" style="top:80px">Contact</h2>
  <div class="field-label" style="left:164px;top:157px">Name</div>
  <div class="field-line" style="left:164px;top:194px;width:423px"></div>
  <div class="field-label" style="left:615px;top:157px">Phone</div>
  <div class="field-line" style="left:615px;top:194px;width:421px"></div>
  <div class="field-label" style="left:164px;top:220px">Email Address</div>
  <div class="field-line" style="left:164px;top:258px;width:423px"></div>
  <div class="field-line" style="left:615px;top:258px;width:421px"></div>
  <div class="field-label" style="left:164px;top:279px">Message</div>
  <div class="field-line" style="left:173px;top:356px;width:872px"></div>
  <a class="btn" style="left:524px;top:392px">Submit</a>
</section>

<footer class="site-footer">
  <div class="copyright">Copyright © 2020. Company Name. All Right Reserved</div>
  <div class="social footer-social" aria-label="Social links"><span></span><span></span><span></span><span></span></div>
</footer>

</body>
</html>
```